BRIGHT RIVER POWER.

I'd like my business logo.
contact name: Dennis Halvorsen
phone:0438759164
email: info@brightriverpower.net.au
website: www.brightriverpower.net.au

services:
solar
battery storage
LED lighting
energy saving solutions
general electrical
I'd like the design to look professional

Target Market(s)

Everyone

Industry/Entity Type

Business

Contact Information for Business Card

as described above

Requirements
Must have
• Id like the colours and the design to work well with my logo.

```html
<!DOCTYPE html>
<html lang="en">
<head>
<meta charset="utf-8">
<title>Bright River Power – Business Card</title>
<link href="https://fonts.googleapis.com/css2?family=Roboto:wght@400;500;700&display=swap" rel="stylesheet">
<style>
  :root {
    --page-bg: #e9e6e1;
    --card-white: #ffffff;
    --card-shade: #f1f1f1;
    --band-green: #9ccc4a;
    --text-green: #6fb23a;
    --accent-orange: #f4a51c;
    --ink-white: #ffffff;
  }
  * { margin: 0; padding: 0; box-sizing: border-box; }
  html, body { width: 1200px; height: 1023px; overflow: hidden; }
  body {
    background: var(--page-bg);
    font-family: "Roboto", Arial, sans-serif;
    position: relative;
  }
  .business-card {
    position: absolute;
    left: 80px; top: 215px;
    width: 1040px; height: 594px;
    border-radius: 26px;
    background: linear-gradient(160deg, var(--card-white) 40%, var(--card-shade) 100%);
    box-shadow: 0 10px 30px rgba(0,0,0,0.18);
    overflow: hidden;
  }
  .brand-lockup {
    position: absolute;
    left: 80px; top: 110px;
    display: flex; align-items: center; gap: 22px;
  }
  .brand-dot {
    width: 70px; height: 70px; border-radius: 50%;
    background: var(--band-green);
  }
  .brand-name {
    font-weight: 700; font-size: 54px; letter-spacing: 1px;
    color: var(--text-green);
  }
  .contact-band {
    position: absolute;
    left: 0; right: 0; top: 262px; height: 148px;
    background: var(--band-green);
    color: var(--ink-white);
    padding: 0 70px;
  }
  .contact-name {
    position: absolute; top: 16px; left: 420px;
    display: flex; align-items: center; gap: 12px;
    font-weight: 700; font-size: 40px;
  }
  .contact-row {
    position: absolute; bottom: 22px; left: 60px; right: 40px;
    display: flex; justify-content: space-between;
    font-size: 25px;
  }
  .contact-item { display: flex; align-items: center; gap: 9px; }
  .contact-item svg, .contact-name svg { flex: none; }
  .services {
    position: absolute; left: 0; right: 0; top: 438px;
    text-align: center;
  }
  .services-title {
    display: inline-flex; align-items: center; gap: 12px;
    color: var(--accent-orange); font-size: 30px; margin-bottom: 12px;
  }
  .services-title::before, .services-title::after {
    content: ""; width: 60px; height: 2px; background: var(--accent-orange);
  }
  .services-list {
    color: var(--text-green); font-size: 27px; line-height: 1.35;
  }
  .services-list .bullet { color: var(--accent-orange); margin: 0 4px 0 10px; }
</style>
</head>
<body>
  <div class="business-card">
    <div class="brand-lockup">
      <span class="brand-dot"></span>
      <span class="brand-name">BRIGHT RIVER POWER</span>
    </div>

    <div class="contact-band">
      <div class="contact-name">
        <svg width="32" height="32" viewBox="0 0 32 32" aria-hidden="true">
          <circle cx="16" cy="16" r="15" fill="#fff"/>
          <circle cx="16" cy="12" r="5" fill="var(--band-green)"/>
          <path d="M7 25c2-5 5-7 9-7s7 2 9 7z" fill="var(--band-green)"/>
        </svg>
        Dennis Halvorsen
      </div>
      <div class="contact-row">
        <span class="contact-item">
          <svg width="24" height="24" viewBox="0 0 24 24" aria-hidden="true">
            <circle cx="12" cy="12" r="10.5" fill="none" stroke="#fff" stroke-width="1.6"/>
            <path d="M9 7l2 2-1 1.5c.8 1.6 2 2.8 3.5 3.5L15 13l2 2-1.5 1.8C11 16 8 13 7.2 8.5z" fill="#fff"/>
          </svg>
          0438759164
        </span>
        <span class="contact-item">
          <svg width="24" height="18" viewBox="0 0 24 18" aria-hidden="true">
            <rect x="1" y="1" width="22" height="16" fill="#fff"/>
            <path d="M1 1l11 9 11-9" fill="none" stroke="var(--band-green)" stroke-width="1.6"/>
          </svg>
          info@brightriverpower.net.au
        </span>
        <span class="contact-item">
          <svg width="24" height="24" viewBox="0 0 24 24" aria-hidden="true" fill="none" stroke="#fff" stroke-width="1.6">
            <circle cx="12" cy="12" r="10"/>
            <ellipse cx="12" cy="12" rx="4.5" ry="10"/>
            <path d="M2 12h20M4 7h16M4 17h16"/>
          </svg>
          www.brightriverpower.net.au
        </span>
      </div>
    </div>

    <div class="services">
      <div class="services-title">Services</div>
      <div class="services-list">
        <div><span class="bullet">●</span>Solar <span class="bullet">●</span>Battery Storage <span class="bullet">●</span>LED lighting</div>
        <div><span class="bullet">●</span>Energy Saving Solutions <span class="bullet">●</span>General Electrical</div>
      </div>
    </div>
  </div>
</body>
</html>
```